Label design for Beard Oil Bottle

Looking for a label design for our new line of beard oils. I attached our logo. Label should include ingredients, usage, logo, under the logo we will have the scent of the beard oil. We currently have 3 different scents.

Scent Names:
Velvet Lantern
Tumbleweed
Kestra

will need to have a section for our website and social media sites.

Example:
Join the Copperline Society!
www.thecopperlinesociety-shop.test
Friendbook
Snapgallery
Chirpline

I just uploaded an example logo!

Target Market(s)

Men with Beards

Industry/Entity Type

Hair And Beauty

Font styles to use
Other font styles liked:
• Same as logo font

Colors
ffffff
000000

Requirements
Must have
• Black label with white writing and white logo

```html
<!DOCTYPE html>
<html lang="en">
<head>
<meta charset="UTF-8">
<title>Copperline Society Beard Oil Label</title>
<link rel="stylesheet" href="https://fonts.googleapis.com/css2?family=Oswald:wght@400;600&family=Roboto+Condensed:wght@400;700&display=swap">
<style>
  :root {
    --backdrop: #ececec;
    --label-black: #1e1e1e;
    --ink-white: #ffffff;
    --ink-soft: #d9d9d9;
  }
  * { box-sizing: border-box; margin: 0; padding: 0; }
  html, body {
    width: 784px;
    height: 1200px;
    overflow: hidden;
    background: var(--backdrop);
  }
  .canvas {
    width: 784px;
    height: 1200px;
    display: flex;
    align-items: center;
    justify-content: center;
  }
  .label {
    position: relative;
    width: 680px;
    height: 900px;
    background: var(--label-black);
    color: var(--ink-white);
    font-family: "Roboto Condensed", "Arial Narrow", sans-serif;
  }
  .info-section {
    position: absolute;
    left: 56px;
    width: 500px;
  }
  .ingredients { top: 60px; }
  .usage { top: 320px; }
  .section-title {
    font-weight: 700;
    font-size: 34px;
    letter-spacing: 0.5px;
    margin-bottom: 16px;
  }
  .section-text {
    font-size: 27px;
    line-height: 1.45;
    color: var(--ink-soft);
  }
  .side-rule {
    position: absolute;
    right: 50px;
    top: 60px;
    width: 24px;
    height: 500px;
  }
  .brand-block {
    position: absolute;
    left: 40px;
    top: 590px;
    display: flex;
    align-items: center;
    gap: 26px;
  }
  .brand-mark {
    width: 160px;
    display: flex;
    flex-direction: column;
    align-items: center;
    gap: 8px;
  }
  .brand-dot {
    width: 56px;
    height: 56px;
    border-radius: 50%;
    background: var(--ink-white);
  }
  .brand-name {
    font-family: "Oswald", "Arial Narrow", sans-serif;
    font-weight: 600;
    font-size: 18px;
    text-align: center;
    line-height: 1.1;
    text-transform: uppercase;
  }
  .scent-name {
    font-family: "Oswald", "Arial Narrow", sans-serif;
    font-weight: 400;
    font-size: 22px;
    letter-spacing: 1px;
    text-transform: uppercase;
    white-space: nowrap;
    margin-top: 4px;
  }
  .community {
    font-family: "Oswald", "Arial Narrow", sans-serif;
  }
  .community-join {
    font-size: 28px;
    font-weight: 400;
  }
  .community-name {
    font-size: 32px;
    font-weight: 600;
    margin-top: 2px;
  }
  .social-list {
    display: flex;
    gap: 14px;
    margin-top: 14px;
    list-style: none;
    font-family: "Roboto Condensed", "Arial Narrow", sans-serif;
    font-size: 17px;
  }
  .divider {
    position: absolute;
    left: 40px;
    right: 40px;
    top: 806px;
    height: 2px;
    background: var(--ink-white);
  }
  .website {
    position: absolute;
    left: 40px;
    top: 826px;
    font-size: 28px;
    letter-spacing: 0.3px;
  }
</style>
</head>
<body>
<div class="canvas">
  <section class="label">
    <div class="info-section ingredients">
      <h2 class="section-title">Ingredients:</h2>
      <p class="section-text">Jojoba Oil, Argan Oil,<br>Grapeseed Oil,Vitamin e Oil,<br>Sweet Orange Oil, Lemon Oil,<br>Clary Sage Oil</p>
    </div>

    <div class="info-section usage">
      <h2 class="section-title">Usage:</h2>
      <p class="section-text">Apply 3-5 drops to palm, rub<br>hands together and work into<br>beard and skin. Comb through.</p>
    </div>

    <svg class="side-rule" viewBox="0 0 24 500" aria-hidden="true">
      <line x1="12" y1="0" x2="12" y2="225" stroke="#ffffff" stroke-width="2"/>
      <rect x="4" y="232" width="16" height="36" fill="#ffffff"/>
      <line x1="12" y1="275" x2="12" y2="500" stroke="#ffffff" stroke-width="2"/>
    </svg>

    <div class="brand-block">
      <div class="brand-mark">
        <span class="brand-dot"></span>
        <span class="brand-name">Copperline<br>Society</span>
        <span class="scent-name">Velvet Lantern</span>
      </div>
      <div class="community">
        <p class="community-join">Join</p>
        <p class="community-name">the Copperline Society!</p>
        <ul class="social-list">
          <li>Friendbook</li>
          <li>Chirpline</li>
          <li>Snapgallery</li>
        </ul>
      </div>
    </div>

    <div class="divider"></div>
    <p class="website">www.thecopperlinesociety-shop.test</p>
  </section>
</div>
</body>
</html>
```